New Technology Company is Launching New Products with a New Website

We want to create a 4-page website in WordPress compatible files to launch our site on HostMeadow. The attached files provide our ideas for Products, Services and About Us pages. We believe the content in those files is about right but the actual design is up to the artist that wants to accept this challenge. Additionally we need a fantastic Home page but we have no idea what that looks like. It obviously needs to lead to the other 3 pages but more importantly it needs to capture the interest of our current and future customers.

Details:
1. Please start off using the text descriptions in the example files. If shorter, longer, different descriptions are needed, just let us know.

2. Please feel free to suggest any photos you can find from free or reasonable stock photo services. Picvault and others like them are reasonable. If you find a perfect image, please send us a link and we will buy a license if its affordable. I have paid ~US$10 per image in the past.

3. I have also uploaded our stationery and logo files. We would like the website design to be consistent with the logo and stationery designs. The stationery designs are all in one file.

We have two logos, and would like to see both of them used on the website. One logo shows the letters KRTV in an outlined shield that is read and blue. That logo is used in the stationery and in our draft website design as a header. The other logo shows flames bouncing off a round shield. Perhaps this logo could be used at the bottom of each page on the website, or some other place where it would be fun and creative without diminishing the seriousness of our underlying science and engineering.

4. We are looking for an artist to have some fun with this and propose something creative. We have lots of boring ideas ourselves so we need YOU to do something else! Thank you so much for considering this challenge!

Target Market(s)

People interested in new, high performance fabrics, including consumers, store owners, garment designers and companies like Wolverock or The Ridge Pelt

Coding

Coded - Design and coding required

Font styles to use
Sans Serif

Colors
f04a51
3277b5

Requirements
Must have
• something unforgetable

```html
<!DOCTYPE html>
<html lang="en">
<head>
<meta charset="utf-8">
<title>KRTV — High Temperature Insulations</title>
<link rel="stylesheet" href="https://fonts.googleapis.com/css2?family=Roboto:wght@400;500;700&family=Open+Sans:wght@400&display=swap">
<style>
:root{
  --blue:#1565a9;
  --brand-blue:#3277b5;
  --red:#d42330;
  --brand-red:#f04a51;
  --ink:#222;
  --muted:#444;
  --rule:#ddd;
  --white:#fff;
}
*{margin:0;padding:0;box-sizing:border-box}
html,body{width:1200px;height:1143px;overflow:hidden;background:var(--white)}
body{position:relative;font-family:'Roboto',sans-serif;color:var(--ink)}
.site-header{position:absolute;left:0;top:0;width:1200px;height:188px}
.header-shapes{position:absolute;left:0;top:0}
.brand{position:absolute;left:148px;top:62px;display:flex;align-items:center;gap:10px}
.brand-mark{width:22px;height:22px;background:var(--red)}
.brand-name{font:700 44px 'Roboto',sans-serif;color:var(--blue);letter-spacing:1px}
.contact-block{position:absolute;left:749px;top:14px;color:var(--white);font-size:15px;line-height:22px}
.contact-block .company{font-size:16px;margin-bottom:1px}
.contact-row{display:flex;align-items:center;gap:5px}
.contact-row svg{flex:none}
.contact-row.indent{padding-left:22px}
.main-nav{position:absolute;top:154px;left:672px;display:flex;gap:0}
.main-nav a{font:500 16px 'Roboto',sans-serif;color:var(--blue);text-decoration:none;position:absolute;white-space:nowrap}
.hero{position:absolute;left:0;top:188px;width:1200px;height:593px;
  background:
    radial-gradient(ellipse 380px 260px at 150px 440px,rgba(240,110,40,.85),transparent 70%),
    radial-gradient(ellipse 360px 420px at 880px 300px,rgba(230,190,40,.8),transparent 70%),
    radial-gradient(ellipse 320px 320px at 960px 520px,rgba(230,80,30,.85),transparent 70%),
    linear-gradient(90deg,#3a2a2a 0%,#6b5356 30%,#8a7880 48%,#a86a4a 70%,#8a4a2a 100%)}
.hero-title{position:absolute;left:0;width:1208px;top:222px;text-align:center;color:var(--white);font:700 49px/49px 'Roboto',sans-serif;letter-spacing:1px;text-shadow:0 1px 3px rgba(0,0,0,.3)}
.slider-controls{position:absolute;left:551px;top:545px;display:flex;align-items:center;gap:4px}
.slider-arrow{width:20px;height:20px;border-radius:50%;background:var(--white);display:flex;align-items:center;justify-content:center}
.slider-dot{width:9px;height:9px;border-radius:50%;background:rgba(255,255,255,.45);margin:0 2px}
.slider-dot.active{background:var(--white)}
.footer-brand{position:absolute;left:124px;top:880px;display:flex;align-items:center;gap:10px}
.footer-brand .dot{width:44px;height:44px;border-radius:50%;background:var(--blue)}
.footer-brand .name{font:700 40px 'Roboto',sans-serif;color:var(--blue)}
.col-rule{position:absolute;top:838px;width:1px;height:176px;background:var(--rule)}
.footer-col{position:absolute;top:840px}
.footer-col h3{font:500 18px 'Roboto',sans-serif;color:var(--ink);margin-bottom:14px;letter-spacing:.2px}
.footer-col ul{list-style:none}
.footer-col li{font:400 12px 'Open Sans',sans-serif;color:var(--muted)}
.col-info li{height:26.4px}
.col-help li,.col-account li{height:28.8px}
.footer-rule{position:absolute;left:11px;top:1056px;width:1152px;height:1px;background:#d6d6d6}
.copyright{position:absolute;left:104px;top:1091px;font:400 12px 'Open Sans',sans-serif;color:var(--muted)}
.social{position:absolute;top:1082px;display:flex;gap:7px;left:901px}
.social span{width:37px;height:37px;border:1px solid #555;border-radius:50%;display:block}
</style>
</head>
<body>
<header class="site-header">
  <svg class="header-shapes" width="1200" height="188" viewBox="0 0 1200 188">
    <path d="M387 0 C440 40 470 90 520 120 C545 136 570 142 600 142 L1200 142 L1200 0 Z" fill="var(--blue)"/>
    <path d="M0 102 C30 110 50 150 100 188 L0 188 Z" fill="var(--red)"/>
  </svg>
  <div class="brand"><span class="brand-mark"></span><span class="brand-name">KRTV</span></div>
  <div class="contact-block">
    <div class="company">K.R. Talbot and Ventures PLLC</div>
    <div class="contact-row"><svg width="17" height="17" viewBox="0 0 17 17"><circle cx="8.5" cy="8.5" r="8.5" fill="#fff"/><path d="M5 4.5l2 0 .8 2.3-1.2.9a6 6 0 0 0 2.7 2.7l.9-1.2 2.3.8v2c0 .5-.5 1-1 1A7.5 7.5 0 0 1 4 5.5c0-.5.5-1 1-1z" fill="var(--blue)"/></svg>555-014-2200</div>
    <div class="contact-row"><svg width="17" height="17" viewBox="0 0 17 17"><circle cx="8.5" cy="8.5" r="8.5" fill="#fff"/><circle cx="8.5" cy="8.5" r="4.5" fill="none" stroke="var(--blue)" stroke-width="1.4"/><path d="M4 8.5h9M8.5 4v9" stroke="var(--blue)" stroke-width="1"/></svg>www.krtvtech.com</div>
    <div class="contact-row"><svg width="17" height="17" viewBox="0 0 17 17"><circle cx="8.5" cy="8.5" r="8.5" fill="#fff"/><path d="M8.5 3.5a3.5 3.5 0 0 1 3.5 3.5c0 2.5-3.5 6.5-3.5 6.5S5 9.5 5 7a3.5 3.5 0 0 1 3.5-3.5z" fill="var(--blue)"/><circle cx="8.5" cy="7" r="1.3" fill="#fff"/></svg>48 W. Alder Ave, Bldg. 2&nbsp; Ridgeford,</div>
    <div class="contact-row indent">Arizona 85099, USA</div>
  </div>
  <nav class="main-nav">
    <a href="#" style="left:0">PRODUCTS</a>
    <a href="#" style="left:114px">SERVICES</a>
    <a href="#" style="left:219px">ABOUT US</a>
    <a href="#" style="left:328px">CONTACT US</a>
  </nav>
</header>

<section class="hero" role="img" aria-label="Firefighters in yellow helmets and orange protective suits spraying water at a fire">
  <h1 class="hero-title">HIGH TEMPERATURE<br>INSULATIONS</h1>
  <div class="slider-controls">
    <span class="slider-arrow"><svg width="8" height="10" viewBox="0 0 8 10"><path d="M6 1L2 5l4 4" fill="none" stroke="#222" stroke-width="1.6"/></svg></span>
    <span class="slider-dot active"></span><span class="slider-dot"></span><span class="slider-dot"></span><span class="slider-dot"></span>
    <span class="slider-arrow"><svg width="8" height="10" viewBox="0 0 8 10"><path d="M2 1l4 4-4 4" fill="none" stroke="#222" stroke-width="1.6"/></svg></span>
  </div>
</section>

<footer>
  <div class="footer-brand"><span class="dot"></span><span class="name">KRTV</span></div>
  <div class="col-rule" style="left:392px"></div>
  <div class="col-rule" style="left:594px"></div>
  <div class="col-rule" style="left:840px"></div>
  <div class="footer-col col-info" style="left:444px">
    <h3>INFORMATION</h3>
    <ul><li>About Us</li><li>Careers</li><li>Privacy &amp; Security</li><li>Site Map</li><li>Terms of Use</li><li>Blog</li></ul>
  </div>
  <div class="footer-col col-help" style="left:646px">
    <h3>HELP &amp; SUPPORT</h3>
    <ul><li>Recommended Reading</li><li>Submit your Story</li><li>Contact Us</li><li>Frequently Asked Questions</li><li>How to Order</li></ul>
  </div>
  <div class="footer-col col-account" style="left:894px">
    <h3>MY ACCOUNT</h3>
    <ul><li>Delivery Information</li><li>My Account</li><li>Order Tracking</li><li>Reminder Service</li><li>Shipping, Returns &amp; Fees</li></ul>
  </div>
  <div class="footer-rule"></div>
  <p class="copyright">Copyright © 2018, KRTV. All Rights Reserved.</p>
  <div class="social">
    <span aria-label="Social link 1"></span><span aria-label="Social link 2"></span><span aria-label="Social link 3"></span><span aria-label="Social link 4"></span>
  </div>
</footer>
</body>
</html>
```